Real Estate Flyer

Hi - I am assisting a relative to sell a unit. I am looking to have a two page flyer designed (configured as a single page with back to back printing). I have uploaded two samples to give you an idea of the look and feel - one which relates to this property when originally purchased, the other for a different property.
The flyer should includes several key photos on the front along with the wording. The rear should include any secondary photos along with the floor plan.
The flyer should be close to A4 size.

Updates
Hi,
Industry/Entity Type
Real Estate
Look and feel
Each slider illustrates characteristics of the customer's brand and the style your logo design should communicate.

```html
<!DOCTYPE html>
<html lang="en">
<head>
<meta charset="utf-8">
<title>Oversized apartment in a lifestyle location – flyer</title>
<link rel="stylesheet" href="https://fonts.googleapis.com/css2?family=Montserrat:wght@400;500;600;700;800&display=swap">
<style>
  :root {
    --purple: #7b2677;
    --grey-text: #5f5f5f;
    --body-text: #6b6b6b;
    --teal: #1aa6c9;
    --header-light: #f4f4f4;
    --header-dark: #d9d9d9;
    --backdrop: #ececec;
    --paper: #ffffff;
  }
  * { box-sizing: border-box; margin: 0; padding: 0; }
  html, body { width: 1200px; height: 1000px; overflow: hidden; }
  body {
    background: var(--backdrop);
    font-family: "Montserrat", Arial, sans-serif;
    color: var(--body-text);
  }
  .flyer {
    position: absolute;
    left: 270px; top: 33px;
    width: 660px; height: 934px;
    background: var(--paper);
    overflow: hidden;
  }
  .flyer__spine {
    position: absolute; left: 0; top: 0;
    width: 24px; height: 100%;
    background: var(--purple);
  }
  .flyer__header {
    position: absolute; left: 24px; right: 0; top: 0;
    height: 58px;
    background: linear-gradient(180deg, var(--header-light), var(--header-dark));
    display: flex; align-items: center; justify-content: space-between;
    padding: 0 22px 0 20px;
  }
  .flyer__address { color: var(--purple); font-weight: 700; font-size: 15px; }
  .features { display: flex; align-items: center; gap: 6px; color: var(--purple); font-weight: 700; font-size: 12px; }
  .features__item { display: flex; align-items: center; gap: 3px; }
  .features__divider { width: 1px; height: 16px; background: #a0a0a0; }
  .flyer__photo {
    position: absolute; left: 24px; right: 0; top: 58px;
    height: 312px;
    background: linear-gradient(180deg, #3d86d6 0%, #8ab7e4 30%, #b86a4a 48%, #d7c2a6 70%, #2fa6c7 100%);
    border-bottom: 5px solid var(--teal);
  }
  .headline { position: absolute; left: 50px; top: 384px; line-height: 1; }
  .headline__lead {
    display: block; color: var(--purple);
    font-weight: 800; font-size: 60px; letter-spacing: 1px;
  }
  .headline__rest {
    display: block; color: var(--grey-text);
    font-weight: 700; font-size: 29px; margin-top: 2px;
  }
  .info-panel {
    position: absolute; right: 0; top: 478px;
    width: 222px; height: 250px;
    background: var(--purple);
    color: #fff;
    padding: 18px 18px;
  }
  .info-panel__block { padding: 12px 0; border-bottom: 1px solid rgba(255,255,255,0.3); }
  .info-panel__block:last-child { border-bottom: none; }
  .info-panel__label { font-size: 12px; font-weight: 500; }
  .info-panel__value { font-size: 16px; font-weight: 700; line-height: 1.25; white-space: nowrap; }
  .info-panel__note { font-size: 9.5px; font-weight: 500; white-space: nowrap; }
  .description {
    position: absolute; left: 50px; top: 492px;
    width: 360px;
    font-size: 10.5px; line-height: 1.45;
  }
  .description strong { color: var(--purple); font-weight: 700; }
  .highlights {
    position: absolute; left: 52px; top: 612px;
    width: 378px;
    list-style: none;
    font-size: 10px; line-height: 1.8;
    letter-spacing: -0.2px;
    white-space: nowrap;
  }
  .highlights li::before { content: "•"; margin-right: 6px; }
  .rates {
    position: absolute; left: 50px; top: 760px;
    color: var(--purple);
    font-size: 12.5px; font-weight: 700; line-height: 1.35;
    border-collapse: collapse;
  }
  .rates td { padding: 0; }
  .rates td:first-child { width: 118px; }
</style>
</head>
<body>
  <article class="flyer">
    <div class="flyer__spine"></div>

    <header class="flyer__header">
      <span class="flyer__address">8/41-47 Laurel Street, WESTON HEIGHTS</span>
      <div class="features">
        <span class="features__item">2
          <svg width="18" height="12" viewBox="0 0 18 12" aria-label="bedrooms"><rect x="1" y="1" width="2" height="10" fill="currentColor"/><rect x="1" y="6" width="16" height="3" fill="currentColor"/><rect x="15" y="6" width="2" height="5" fill="currentColor"/><rect x="4" y="3" width="4" height="3" rx="1" fill="currentColor"/></svg>
        </span>
        <span class="features__divider"></span>
        <span class="features__item">1
          <svg width="16" height="12" viewBox="0 0 16 12" aria-label="bathrooms"><rect x="1" y="5" width="14" height="4" rx="1" fill="currentColor"/><rect x="2" y="1" width="2" height="5" fill="currentColor"/><rect x="3" y="9" width="2" height="2" fill="currentColor"/><rect x="11" y="9" width="2" height="2" fill="currentColor"/></svg>
        </span>
        <span class="features__divider"></span>
        <span class="features__item">1
          <svg width="18" height="12" viewBox="0 0 18 12" aria-label="car spaces"><path d="M3 5 L5 1 H13 L15 5 H17 V9 H1 V5 Z" fill="currentColor"/><circle cx="5" cy="10" r="1.8" fill="currentColor"/><circle cx="13" cy="10" r="1.8" fill="currentColor"/></svg>
        </span>
      </div>
    </header>

    <div class="flyer__photo" role="img" aria-label="Photo of the apartment building's brick balconies above a rooftop swimming pool under blue sky"></div>

    <h1 class="headline">
      <span class="headline__lead">OVERSIZED</span>
      <span class="headline__rest">apartment in a lifestyle location</span>
    </h1>

    <aside class="info-panel">
      <div class="info-panel__block">
        <div class="info-panel__label">Estimated Market Rental:</div>
        <div class="info-panel__value">$700.00 p/w</div>
      </div>
      <div class="info-panel__block">
        <div class="info-panel__label">Inspect :</div>
        <div class="info-panel__value">Sat 10:45 – 11:30;<br>Wed 12:00 – 12:30</div>
      </div>
      <div class="info-panel__block">
        <div class="info-panel__label">Contact:</div>
        <div class="info-panel__value">Daniel Pryor</div>
        <div class="info-panel__note">(Assisting owner in Private Sale)</div>
        <div class="info-panel__value">0400 555 182</div>
      </div>
    </aside>

    <section class="description">
      <p><strong>Peacefully positioned</strong> on the 5th floor of a refurbished security building, this superbly spacious residence combines modern, low maintenance apartment living with inviting prospects for the entertainer.</p>
      <p>Boasting a huge full-width terrace on-title, its sought-after setting in the heart of Weston Heights offers the ultimate in lifestyle and convenience.</p>
    </section>

    <ul class="highlights">
      <li>Expansive open plan living and dining area</li>
      <li>Terrace features city and Botany Bay glimpses</li>
      <li>Kitchen updated with Vellaro gas appliances</li>
      <li>Built-ins in both bedrooms, fully tiled bathrooms</li>
      <li>Internal laundry, secure parking, lift, outdoor pool and gymnasium</li>
      <li>Steps to station, Eastgate and Carrington Park</li>
    </ul>

    <table class="rates">
      <tr><td>Water Rates:</td><td>To be provided on finalizing design</td></tr>
      <tr><td>Council Rates:</td><td>To be provided on finalizing design</td></tr>
      <tr><td>Strata Rates:</td><td>To be provided on finalizing design</td></tr>
    </table>
  </article>
</body>
</html>
```